Redesign Local Plumber Website

redesign of existing plumbing website

Mobile Responsive
Professional
modern
easy enquiry
Map embed

Please see existing site for text and images. Please feel free to suggest improvements and any additional features
callthepipeteam.com.au

attached is logo and the Australian owned badge which we also want featuring

Target Market(s)

Plumbing & Gas Services

Industry/Entity Type

Plumbing

Font styles to use
Sans Serif

Requirements
Must have
• existing logo
Nice to have
• new design
Should not have
• same design

```html
<!DOCTYPE html>
<html lang="en">
<head>
<meta charset="utf-8">
<title>Call The Pipe Team – Plumbing &amp; Gas</title>
<link href="https://fonts.googleapis.com/css2?family=Roboto:wght@400;500;700&family=Open+Sans:wght@400;600&display=swap" rel="stylesheet">
<style>
:root{
  --blue:#1b8ad3;
  --navy:#1a0f55;
  --navy-deep:#0f0840;
  --ink:#111;
  --text:#555;
  --client:#444;
  --light:#f0f0f0;
  --footer:#1d1d1d;
  --white:#fff;
}
*{box-sizing:border-box;margin:0;padding:0}
html,body{width:1200px;height:4566px;overflow:hidden}
body{position:relative;font-family:"Open Sans",sans-serif;color:var(--text);background:var(--white)}
.abs{position:absolute}
h1,h2,h3,h4,.nav,.btn{font-family:"Roboto",sans-serif}
.topbar{left:0;top:0;width:1200px;height:58px;background:var(--blue);color:var(--white);font-family:"Roboto",sans-serif}
.topbar .mail{left:90px;top:20px;font-size:15px;font-weight:500}
.topbar .call{right:90px;top:16px;font-size:22px;font-weight:500}
.header{left:0;top:58px;width:1200px;height:114px;background:var(--white)}
.logo{left:90px;top:32px;display:flex;align-items:center;gap:12px}
.logo .mark{width:48px;height:48px;border-radius:50%;background:var(--blue)}
.logo .name{font-family:"Roboto",sans-serif;font-weight:700;font-size:23px;color:var(--blue);letter-spacing:.3px}
.nav{left:458px;top:52px;display:flex;gap:28px;font-size:18px;font-weight:500;color:var(--ink)}
.drop{left:476px;top:22px}
.hero{left:0;top:172px;width:1200px;height:565px;background:linear-gradient(135deg,#8d8c8a,#5a5b60 50%,#3c3f4a)}
.hero-copy{left:0;top:168px;width:1200px;text-align:center;color:var(--white)}
.hero-copy h1{font-size:48px;font-weight:500;letter-spacing:.5px}
.hero-copy p{font-size:21px;line-height:32px;margin-top:14px}
.btn{display:inline-block;text-align:center;font-weight:500}
.btn-blue{background:var(--blue);color:var(--white)}
.hero .start{left:494px;top:328px;width:213px;height:58px;line-height:58px;font-size:21px}
.sec-title{left:0;width:1200px;text-align:center;font-size:40px;font-weight:500;color:var(--ink)}
.intro{left:90px;top:908px;width:560px;font-size:17.5px;line-height:36px}
.photo{background:linear-gradient(135deg,#b9b3ab,#6a645e)}
.intro-photo{left:714px;top:895px;width:394px;height:385px;background:linear-gradient(135deg,#c9c2b8,#7b6f66 60%,#3b3734)}
.intro .more{display:block;width:187px;height:57px;line-height:57px;font-size:19px;margin-top:20px}
.card{top:1344px;width:327px;height:372px;background:var(--light);text-align:center}
.card .pic{position:absolute;left:8px;top:9px;width:311px;height:178px}
.card h3{position:absolute;top:201px;left:0;width:100%;font-size:19px;font-weight:500;color:var(--ink)}
.card p{position:absolute;top:236px;left:22px;width:283px;font-size:13.5px;line-height:26px}
.card .mini{position:absolute;left:106px;top:322px;width:114px;height:32px;line-height:32px;font-size:14px}
.card .cards{position:absolute;left:122px;top:338px;display:flex;gap:4px}
.card .cards span{width:40px;height:22px;background:#c9c9c9;border-radius:2px}
.about{left:0;top:1806px;width:1200px;height:438px;background:var(--navy)}
.about .circle{left:88px;top:26px;width:366px;height:366px;border-radius:50%;background:linear-gradient(135deg,#d7dbe2,#6d88b5 60%,#263c74)}
.about h2{left:489px;top:46px;font-size:40px;font-weight:500;color:var(--white)}
.about p{left:489px;top:100px;width:622px;font-size:17.5px;line-height:36px;color:#e6e4f2}
.badge{display:inline-block;vertical-align:middle;background:#e8e8e8}
.badge.round{width:40px;height:36px;border-radius:4px}
.badge.flat{width:112px;height:30px;background:#7cc34a}
.outline{border:1.5px solid var(--white);color:var(--white)}
.about .more{left:479px;top:337px;width:164px;height:50px;line-height:47px;font-size:19px}
.services-sub{left:0;top:2398px;width:1200px;text-align:center;font-size:21px;line-height:33px;color:#333}
.plumb-band{left:0;top:2503px;width:750px;height:90px;background:var(--blue)}
.plumb{left:0;top:2593px;width:633px;height:332px;background:var(--blue)}
.plumb-copy{left:90px;top:2538px;width:480px;color:var(--white)}
.plumb-copy h3,.gas-copy h3{font-size:26px;font-weight:500}
.plumb-copy p,.plumb-copy li,.gas-copy p,.gas-copy li{font-size:16px;line-height:27px}
.plumb-copy p{margin-top:10px}
ul{list-style:none}
li{position:relative;padding-left:22px}
li::before{content:"";position:absolute;left:2px;top:11px;width:7px;height:7px;border-radius:50%;background:currentColor}
.plumb-copy .more,.gas-copy .more{display:inline-block;margin-top:14px;width:120px;height:33px;line-height:31px;font-size:15px}
.plumb-photo{left:633px;top:2593px;width:471px;height:332px;background:linear-gradient(135deg,#d5d1cc,#9a8f84 55%,#4a4540)}
.gas-photo{left:89px;top:2925px;width:544px;height:382px;background:linear-gradient(135deg,#e0ddd8,#a39b92 55%,#5a524a)}
.gas{left:541px;top:2925px;width:659px;height:430px;background:var(--navy-deep)}
.gas-copy{left:674px;top:2968px;width:440px;color:#e8e6f3}
.gas-copy p{margin-top:10px}
.gas-copy ul{margin-top:14px}
.gas-copy li{line-height:32px}
.clients{left:0;top:3535px;width:1200px;display:flex;justify-content:center;gap:92px}
.client{display:flex;align-items:center;gap:10px;font-family:"Open Sans",sans-serif;font-weight:600;font-size:30px;color:var(--client)}
.client i{width:26px;height:26px;display:block;background:#bbb}
.dots{left:564px;top:3634px;display:flex;gap:6px}
.dots span{width:9px;height:9px;border-radius:50%;background:#111}
.dots span.on{background:var(--blue)}
.map{left:0;top:3736px;width:1200px;height:429px;background:linear-gradient(160deg,#ececec,#dedede)}
.contact{left:90px;top:3777px;width:490px;height:333px;background:var(--blue)}
.contact h2{position:absolute;top:32px;width:100%;text-align:center;color:var(--white);font-size:26px;font-weight:500}
.field{position:absolute;background:var(--white);font-size:11px;color:#444;padding:6px 6px}
.submit{position:absolute;left:178px;top:282px;width:126px;height:34px;line-height:32px;font-size:12px}
.place{left:652px;top:3948px;width:305px;height:100px;background:var(--white)}
.place .face{position:absolute;left:0;top:0;width:100px;height:100px;background:linear-gradient(135deg,#c6d2e2,#6c84a8)}
.place h4{position:absolute;left:112px;top:20px;font-size:14px;color:#111}
.place p{position:absolute;left:112px;top:42px;font-size:13px;line-height:22px;color:#333}
.pin{left:742px;top:3880px;display:flex;gap:4px;font-size:13px;color:#c1272d;line-height:16px}
.footer{left:0;top:4165px;width:1200px;height:401px;background:var(--footer);color:#ddd}
.footer h4{font-size:21px;font-weight:400;color:var(--white)}
.fcol{position:absolute;top:58px}
.fcol p{font-size:15px;line-height:32px;margin-top:10px}
.fcol .links{margin-top:10px;font-size:15px;line-height:32px}
.fcol.news{width:340px}
.fcol.news p{font-size:14px;line-height:27px}
.news-form{display:flex;margin-top:18px;width:336px;height:47px;border:2px solid var(--white)}
.news-form span{flex:1;background:var(--white);color:#666;font-size:14px;padding:13px 12px}
.news-form b{width:130px;background:var(--blue);color:var(--white);font-family:"Roboto",sans-serif;font-weight:500;font-size:18px;text-align:center;line-height:43px}
.owned{left:588px;top:4340px;width:122px;height:122px;border-radius:50%;background:#2f7a3a;border:5px solid var(--white)}
.rule{left:0;top:4486px;width:1200px;height:1px;background:#444}
.copy{left:90px;top:4518px;font-size:16px;color:#ddd}
.social{left:970px;top:4522px;display:flex;gap:14px}
.social span{width:20px;height:20px;border-radius:50%;background:#eee;display:block}
</style>
</head>
<body>

<div class="abs topbar">
  <div class="abs mail">OFFICE@CALLTHEPIPETEAM.COM.AU</div>
  <div class="abs call">FREE CALL: 1800 555 019</div>
</div>

<header class="abs header">
  <div class="abs logo"><span class="mark"></span><span class="name">CALL THE PIPE TEAM</span></div>
  <svg class="abs drop" width="18" height="24" viewBox="0 0 18 24" aria-hidden="true"><path d="M9 0C9 0 0 11 0 16a9 8 0 0 0 18 0C18 11 9 0 9 0z" fill="#1b8ad3"/></svg>
  <nav class="abs nav"><span>HOME</span><span>ABOUT US</span><span>SERVICES</span><span>SEPTICS</span><span>PRODUCTS</span><span>CONTACT US</span></nav>
</header>

<section class="abs hero" role="img" aria-label="Plumber kneeling under a kitchen sink with a red toolbox">
  <div class="abs hero-copy">
    <h1>CALL THE PIPE TEAM</h1>
    <p>As a family owned and operated business we are now proud to<br>service the metro and country areas in the northern suburbs.</p>
  </div>
  <span class="abs btn btn-blue start">GET STARTED</span>
</section>

<h2 class="abs sec-title" style="top:815px">PLUMBING &amp; GAS SERVICES</h2>
<div class="abs intro">
  <p>Call The Pipe Team is a family run business based in Harlow since 2004, we service Midland to Wannamal, Ellenbrook to Brigadoon, Joondalup and Wanneroo to Bullsbrook, Toodyay to Gingin, Chittering and surrounding areas of Bullsbrook, Brigadoon, Ellenbrook, Averley, Henley Brook, Millendon, Gingin, Bindoon, Wannamal, Chittering, Midland, Upper Swan, Belhus, Wanneroo, Wangara, Malaga and The Vines. All of our plumbing and gas services are fully licensed.</p>
  <span class="btn btn-blue more">READ MORE</span>
</div>
<div class="abs intro-photo" role="img" aria-label="Gloved hands tightening copper pipe fittings with a spanner"></div>

<div class="abs card" style="left:90px">
  <div class="pic photo" role="img" aria-label="Plumber servicing a hot water system"></div>
  <h3>QUICK RESPONSE</h3>
  <p>If you've had enough of trades people who never turn up when they say they will, call Daniel at Call The Pipe Team.</p>
  <span class="btn btn-blue mini">READ MORE</span>
</div>
<div class="abs card" style="left:438px">
  <div class="pic" style="background:linear-gradient(135deg,#9aa3b0,#3b4250)" role="img" aria-label="Hand pressing pay on a phone"></div>
  <h3>PAYMENT OPTIONS</h3>
  <p style="line-height:23px">Electronic Transfer and all major credit cards accepted, Debit Cards and card terminal facilities, Credit account to approved clients only, All accounts are COD unless by prior.</p>
  <div class="cards" aria-hidden="true"><span></span><span></span></div>
</div>
<div class="abs card" style="left:785px">
  <div class="pic" style="background:linear-gradient(135deg,#d99a5a,#a65a2a 60%,#d8d8d8)" role="img" aria-label="Red toolbox beside a gas water heater"></div>
  <h3>VIEW OUR SHOWROOM</h3>
  <p>We handle all plumbing and gas installation including domestic and commercial. We handle all plumbing and gas installation</p>
  <span class="btn btn-blue mini">READ MORE</span>
</div>

<section class="abs about">
  <div class="abs circle" role="img" aria-label="Tradesman in cap and mask writing on a clipboard"></div>
  <h2 class="abs">ABOUT US</h2>
  <p class="abs">Daniel has been in the plumbing and gas industry since high school, his father Ray was a plumber and estimator. Daniel has trained with reputable plumbers of his time and achieved apprentice of the year 2 years running, then taking out the “Apprentice of the Year” award for all trades during his apprenticeship. A member of Trade Guild <span class="badge round" aria-label="Trade Guild badge"></span> and an Green Pipe Plumber <span class="badge flat" aria-label="Green Pipe badge"></span> Daniel maintains a high level of education.</p>
  <span class="abs btn outline more">READ MORE</span>
</section>

<h2 class="abs sec-title" style="top:2325px">SERVICES</h2>
<p class="abs services-sub">At Call The Pipe Team we have a whole series of goods<br>solutions specially designed for our clients.</p>

<div class="abs plumb-band"></div>
<div class="abs plumb"></div>
<div class="abs plumb-copy">
  <h3>PLUMBING</h3>
  <p>Set-up all pipework for new housing or renovations including compliance paperwork.<br>Installation of tap ware and fixtures:</p>
  <ul>
    <li>Taps</li>
    <li>Sinks – Kitchen Bathroom and Laundry. BBQ areas</li>
    <li>Toilets</li>
    <li>Baths</li>
    <li>Showers – cubical or screens</li>
    <li>Installation of dishwashers and washing machines</li>
  </ul>
  <span class="btn outline more">READ MORE</span>
</div>
<div class="abs plumb-photo" role="img" aria-label="Plumber adjusting valves on a pipe manifold"></div>

<div class="abs gas"></div>
<div class="abs gas-photo" role="img" aria-label="Technician installing a wall mounted gas boiler"></div>
<div class="abs gas-copy">
  <h3>GAS</h3>
  <p>Lorem ipsum dolor sit amet, consectetur adipiscing elit, sed do eiusmod tempor incididunt ut labore et dolore magna aliqua.</p>
  <ul>
    <li>All gas pipework installations to kitchen, heaters, BBQ's and Hot water Units</li>
    <li>Supply and install gas Hot Water Units</li>
    <li>Leak detection, gas line installation and repairs</li>
    <li>Gas appliance installation</li>
  </ul>
  <span class="btn outline more">READ MORE</span>
</div>

<h2 class="abs sec-title" style="top:3440px;font-size:34px">OUR HAPPY CLIENTS</h2>
<div class="abs clients">
  <div class="client"><i></i>Sunfield</div>
  <div class="client"><i></i>Heatwise</div>
  <div class="client"><i></i>Citrus Pumps</div>
</div>
<div class="abs dots"><span></span><span class="on"></span><span></span></div>

<section class="abs map" role="img" aria-label="Street map around the workshop"></section>
<div class="abs pin">
  <svg width="22" height="30" viewBox="0 0 22 30" aria-hidden="true"><path d="M11 0a11 11 0 0 0-11 11c0 8 11 19 11 19s11-11 11-19A11 11 0 0 0 11 0z" fill="#d7262e"/><circle cx="11" cy="11" r="4" fill="#fff"/></svg>
  <span>Call The<br>Pipe Team</span>
</div>
<div class="abs place">
  <div class="face" role="img" aria-label="Team member portrait"></div>
  <h4>Call The Pipe Team</h4>
  <p>27 Kestrel St, Harlow<br>WA 6100, Australia</p>
</div>
<form class="abs contact">
  <h2>CONTACT US</h2>
  <div class="field" style="left:24px;top:83px;width:214px;height:35px">First name</div>
  <div class="field" style="left:252px;top:83px;width:214px;height:35px">Phone</div>
  <div class="field" style="left:24px;top:126px;width:214px;height:35px">Email</div>
  <div class="field" style="left:252px;top:126px;width:214px;height:35px">Address</div>
  <div class="field" style="left:24px;top:170px;width:442px;height:104px">Enter your comment on the side</div>
  <span class="btn outline submit">SUBMIT</span>
</form>

<footer class="abs footer">
  <div class="fcol" style="left:90px;width:290px">
    <h4>CONTACT US</h4>
    <p>27 Kestrel Street, Harlow WA 6100<br>PO Box 88 Harlow WA 6100<br>1800 555 019<br>Office@callthepipeteam.com.au</p>
  </div>
  <div class="fcol" style="left:406px">
    <h4>QUICKS LINKS</h4>
    <div class="links">Home<br>About Us<br>Services<br>Septics<br>Products<br>Contact Us</div>
  </div>
  <div class="fcol" style="left:610px">
    <h4>SERVICES</h4>
    <div class="links">Plumbling<br>Gas</div>
  </div>
  <div class="fcol news" style="left:773px">
    <h4>NEWS LETTER</h4>
    <p>We have a wide range of products to suite any budget, the have the experience to get the job done and we come</p>
    <div class="news-form"><span>Enter the Email</span><b>SEND</b></div>
  </div>
</footer>
<div class="abs owned" aria-label="Australian owned badge"></div>
<div class="abs rule"></div>
<div class="abs copy">Copyright © 2020 Call The Pipe Team . All Rights Reserved.</div>
<div class="abs social" aria-label="Social links"><span></span><span></span><span></span><span></span></div>

</body>
</html>
```